Vantor Ridge needs a Business Card Design

We need a business card design for an Information Technology company based in Fairfax Virginia called Vantor Ridge. We want the business card to use our logo colors. We need it to be double-sided. The business card needs to look professional but we would like it to be unique. You can get company information from our web site (http://www.vantorridgellc.example).

Target Market(s)

Target market is Government Agencies and Business Professionals.

Industry/Entity Type

Business

Requirements
Must have
• Must have section for company name, company address, company URL, employee name, title, phone and email. Also must have company logo and space for entering logos.

```html
<!DOCTYPE html>
<html lang="en">
<head>
<meta charset="utf-8">
<title>Vantor Ridge — Business Card</title>
<link href="https://fonts.googleapis.com/css2?family=Open+Sans:wght@400;600;700&display=swap" rel="stylesheet">
<style>
  :root{
    --navy:#2e3192;
    --blue:#0a72bb;
    --ink:#4a4a4a;
    --muted:#666;
    --paper:#ffffff;
    --stage:#2a2a2a;
  }
  *{box-sizing:border-box;margin:0;padding:0}
  html,body{width:1200px;height:1164px;overflow:hidden}
  body{background:var(--stage);font-family:"Open Sans",Arial,sans-serif;color:var(--ink);position:relative}
  .card{position:absolute;left:160px;width:880px;height:503px;background:var(--paper);overflow:hidden}
  .card--front{top:60px}
  .card--back{top:601px}

  .brand{display:flex;align-items:center;gap:16px}
  .brand__mark{width:46px;height:46px;background:var(--navy);flex:none}
  .brand__name{font-weight:700;color:var(--navy);text-transform:uppercase;letter-spacing:1px;line-height:1;white-space:nowrap}
  .brand__tagline{font-size:11px;font-weight:600;color:var(--muted);text-transform:uppercase;letter-spacing:.6px;margin-top:4px;white-space:nowrap}

  .card--front .brand{position:absolute;left:50%;top:50%;transform:translate(-50%,-60%)}
  .card--front .brand__mark{width:64px;height:64px}
  .card--front .brand__name{font-size:44px}
  .card--front .brand__tagline{font-size:14px}
  .front__url{position:absolute;right:60px;bottom:40px;font-size:16px;color:var(--muted)}
  .front__url b{color:var(--navy);font-weight:600}

  .card--back .brand{position:absolute;left:260px;top:90px}
  .card--back .brand__name{font-size:34px}

  .person{position:absolute;left:70px;top:292px;display:flex;align-items:stretch}
  .person__rule{width:5px;background:var(--navy);margin-right:6px}
  .person__bar{background:var(--navy);color:#fff;padding:7px 16px;font-size:18px;display:flex;gap:18px;white-space:nowrap}
  .person__name{font-weight:700}

  .address{position:absolute;left:86px;top:360px;font-size:17px;line-height:1.3;display:flex;gap:8px}
  .contact{position:absolute;left:392px;top:262px;font-size:16px;line-height:1.35;list-style:none}
  .contact li,.web li{display:flex;align-items:center;gap:7px;white-space:nowrap}
  .web{position:absolute;left:600px;top:218px;font-size:15px;line-height:1.45;list-style:none}
  .social{display:flex;gap:4px;margin-left:4px}
  .social span{width:16px;height:16px;background:var(--blue);display:block}
  .social span:last-child{background:#888}
  .icon{width:14px;height:14px;flex:none;fill:var(--navy)}
  .icon--blue{fill:var(--blue)}

  .band{position:absolute;bottom:0}
  .band--navy{left:0;width:530px;height:72px;background:var(--navy);clip-path:polygon(0 70%,100% 0,100% 100%,0 100%)}
  .band--blue{right:0;width:300px;height:30px;background:var(--blue)}
</style>
</head>
<body>

<section class="card card--front" aria-label="Card front">
  <div class="brand">
    <span class="brand__mark"></span>
    <div>
      <div class="brand__name">Vantor Ridge</div>
      <div class="brand__tagline">Engineering ideas into working systems</div>
    </div>
  </div>
  <p class="front__url">www.<b>vantorridgellc</b>.example</p>
</section>

<section class="card card--back" aria-label="Card back">
  <div class="brand">
    <span class="brand__mark"></span>
    <div>
      <div class="brand__name">Vantor Ridge</div>
      <div class="brand__tagline">Engineering ideas into working systems</div>
    </div>
  </div>

  <div class="person">
    <span class="person__rule"></span>
    <div class="person__bar"><span class="person__name">Samir Haddad</span><span>Job Title</span></div>
  </div>

  <div class="address">
    <svg class="icon" viewBox="0 0 16 16" style="margin-top:4px"><path d="M8 1 0 8h2v7h4v-5h4v5h4V8h2z"/></svg>
    <div>1840 Meridian Ave,<br>Suite 310<br>Fairfax, VA 22030</div>
  </div>

  <ul class="contact">
    <li><svg class="icon" viewBox="0 0 16 16"><path d="M3 1l3 3-2 2c1 2 4 5 6 6l2-2 3 3-2 2C7 15 1 9 1 3z"/></svg>877.555.0142</li>
    <li><svg class="icon" viewBox="0 0 16 16"><rect x="2" y="6" width="12" height="8"/><rect x="4" y="1" width="8" height="5"/></svg>888.555.0187</li>
    <li><svg class="icon" viewBox="0 0 16 16"><path d="M1 3h14v10H1z M1 3l7 6 7-6" fill="none" stroke="#2e3192" stroke-width="1.6"/></svg>name@vantorridgellc.example</li>
  </ul>

  <ul class="web">
    <li><svg class="icon icon--blue" viewBox="0 0 16 16"><circle cx="8" cy="8" r="7"/></svg>www.vantorridgellc.example</li>
    <li>Follow Us On : <span class="social" aria-label="Social profiles"><span></span><span></span><span></span><span></span></span></li>
  </ul>

  <div class="band band--navy"></div>
  <div class="band band--blue"></div>
</section>

</body>
</html>
```